KAJU Freightways #ALLKAJU Business Cards & Letterhead

I am looking to business cards designed for our organization. We are currently undergoing a small re-branding that is taking place. Our organization is called KAJU Freightways and we are headquartered in Phoenix, AZ. We primarily provide transportation and logistics services to the Marlow Parcel Bureau who is our largest customer. I would like to see a design that incorporates name, title, contact info, website, and address (this will be different depending on the employee). I would also like to see some color on the business card using our logo colors or a variation. I would like our logo on the back of the business card with the website displayed. The final design should communicate that we are a next generation transportation operate that focuses on being driver-first, customer-centric, innovative, and sustainable.We would also like our #ALLKAJU catch phrase incorporated as well.

Target Market(s)

Transportation & Logistics

Industry/Entity Type

Trucking Company

Contact Information for Business Card

-First and Last Name
-Position Title
-Contact Phone
-Contact Email
-Physical Address

Font styles to use
Serif

Colors

Designer to choose colors to be used in the design.

Requirements
Must have
• -KAJU logo prominently displayed
• -#ALLKAJU catch phrase used
• -Some amount of color, design gradient, etc.
• -Logo on the back with website listed (https://www.kajufreightco.example)

```html
<!DOCTYPE html>
<html lang="en">
<head>
<meta charset="utf-8">
<title>KAJU Freightways Business Card</title>
<link rel="stylesheet" href="https://fonts.googleapis.com/css2?family=Roboto+Slab:wght@400;500;800&display=swap">
<style>
  :root {
    --bg: #2a2a2c;
    --card: #ffffff;
    --teal: #063d4a;
    --green: #7dc242;
    --green-faint: #eef6e6;
    --grey-faint: #e4e5e8;
    --text: #0b3440;
  }
  * { box-sizing: border-box; margin: 0; padding: 0; }
  html, body { width: 1200px; height: 1200px; overflow: hidden; }
  body {
    background: var(--bg);
    font-family: "Roboto Slab", Georgia, serif;
    color: var(--text);
    position: relative;
  }
  .card {
    position: absolute;
    left: 150px;
    width: 900px;
    height: 514px;
    background: var(--card);
    overflow: hidden;
    box-shadow: 0 12px 30px rgba(0,0,0,.45);
  }
  .card--back { top: 60px; }
  .card--contact { top: 626px; }

  .band {
    position: absolute;
    top: 0;
    width: 180px;
    background: var(--teal);
  }
  .brand-name {
    position: absolute;
    display: flex;
    align-items: center;
    gap: 14px;
  }
  .brand-name__dot {
    width: 34px;
    height: 34px;
    border-radius: 50%;
    background: var(--green);
    flex: none;
  }
  .brand-name__text {
    font-weight: 800;
    font-size: 56px;
    line-height: 1;
    color: var(--teal);
  }

  .card--back .band { left: 360px; height: 170px; }
  .card--back .brand-name { left: 0; right: 0; top: 210px; justify-content: center; }
  .website {
    position: absolute;
    left: 0; right: 0;
    top: 330px;
    text-align: center;
    font-size: 21px;
    font-weight: 500;
  }
  .accent { color: var(--green); }

  .card--contact .band { left: 60px; height: 150px; }
  .card--contact .brand-name { left: 60px; top: 185px; }

  .ring-deco {
    position: absolute;
    left: 440px; top: -40px;
    width: 520px; height: 520px;
    border-radius: 50%;
    border: 14px solid var(--green-faint);
  }
  .wordmark-deco {
    position: absolute;
    left: 470px; top: 40px;
    font-weight: 800;
    font-size: 140px;
    line-height: 1;
    color: var(--grey-faint);
  }
  .person { position: absolute; left: 480px; top: 222px; }
  .person__name { font-size: 32px; font-weight: 800; }
  .person__title { font-size: 21px; color: var(--green); margin-top: 2px; }
  .address {
    position: absolute;
    left: 480px; top: 312px;
    font-size: 18px;
    line-height: 1.35;
  }
  .contacts {
    position: absolute;
    left: 480px; top: 378px;
    list-style: none;
  }
  .contact-line {
    display: flex;
    align-items: center;
    gap: 12px;
    font-size: 20px;
    height: 38px;
  }
  .contact-line svg { width: 26px; height: 26px; flex: none; }
  .company {
    position: absolute;
    left: 60px; top: 390px;
    font-size: 40px;
    font-weight: 800;
  }
  .hashtag {
    position: absolute;
    left: 60px; top: 448px;
    font-size: 20px;
    font-weight: 500;
    color: var(--green);
    letter-spacing: 1px;
  }
</style>
</head>
<body>

<section class="card card--back">
  <div class="band"></div>
  <div class="brand-name"><span class="brand-name__dot"></span><span class="brand-name__text">KAJU</span></div>
  <p class="website">www.<span class="accent">kajufreightco</span>.example</p>
</section>

<section class="card card--contact">
  <div class="ring-deco"></div>
  <div class="wordmark-deco" aria-hidden="true">KAJU</div>
  <div class="band"></div>
  <div class="brand-name"><span class="brand-name__dot"></span><span class="brand-name__text">KAJU</span></div>

  <div class="person">
    <p class="person__name">Dana Whitlow</p>
    <p class="person__title">Director</p>
  </div>
  <p class="address">4120 North Cactus Ridge Boulevard<br>Phoenix, AZ 85019</p>

  <ul class="contacts">
    <li class="contact-line">
      <svg viewBox="0 0 26 26"><circle cx="13" cy="13" r="11.5" fill="none" stroke="#7dc242" stroke-width="2"/><path d="M9 7c-1 1-1.5 2.5-.5 5s3 5 5.5 6.5 3.5.8 4.3-.2l-2.2-2.2-1.6 1c-1.5-.8-3-2.5-3.8-4l1-1.6z" fill="#7dc242"/></svg>
      <span>602-555-0148</span>
    </li>
    <li class="contact-line">
      <svg viewBox="0 0 26 26"><circle cx="13" cy="13" r="11.5" fill="none" stroke="#7dc242" stroke-width="2"/><rect x="7" y="9" width="12" height="8" fill="#7dc242"/><path d="M7 9l6 5 6-5" fill="none" stroke="#fff" stroke-width="1.2"/></svg>
      <span>info@kajufreightco.example</span>
    </li>
    <li class="contact-line">
      <svg viewBox="0 0 26 26"><circle cx="13" cy="13" r="11.5" fill="none" stroke="#7dc242" stroke-width="2"/><circle cx="13" cy="13" r="7" fill="none" stroke="#7dc242" stroke-width="1.4"/><ellipse cx="13" cy="13" rx="3" ry="7" fill="none" stroke="#7dc242" stroke-width="1.2"/><path d="M6 13h14M7.5 9.5h11M7.5 16.5h11" stroke="#7dc242" stroke-width="1"/></svg>
      <span>www.<span class="accent">kajufreightco</span>.example</span>
    </li>
  </ul>

  <p class="company">KAJU <span class="accent">Freightways</span></p>
  <p class="hashtag">#ALLKAJU</p>
</section>

</body>
</html>
```